Redesign This Psychology Website

We would like a slight redesign of this successful psychology (relationship counselling) website:

www.TheKelvaleClinic.com.au

We are updating the website, and we'd like a slight refresh of the design and style.

Please keep to very similar colours, and use the same logo. We're looking for around 10 page templates, however the main one is the home page.

Keep in mind, this website already converts quite well, so we want a new, fresh design in keeping with this one. Please don't bother designing something too extremely different.

thanks :)

Target Market(s)

couples who are looking for relationship counselling. Men and women, 25 - 70, across Australia

Industry/Entity Type

Psychology

Number of Pages Required

5+ page

Font styles to use
Sans Serif

Colors
87cfc6
b7a5cd
ec1f27
ffffff
cee9f5

Requirements
Must have
• a similar look to the current design, just looking for a slight refresh.
• Search bar
• Areas for lots of photos
• same logo
• lots of content areas
Nice to have
• great content areas, where we can display a lot of content and our areas.
Should not have
• no colors like orange, etc.
• should not have a totally different feel.

```html
<!DOCTYPE html>
<html lang="en">
<head>
<meta charset="utf-8">
<title>The Kelvale Clinic – Relationship Counselling</title>
<link href="https://fonts.googleapis.com/css2?family=Open+Sans:wght@400;600;700&family=Red+Hat+Display:wght@500;700;800&display=swap" rel="stylesheet">
<style>
:root{
  --teal:#1b8791;
  --teal-dark:#146c74;
  --red:#e8232a;
  --ink:#222;
  --body:#555;
  --muted:#888;
  --light-blue:#cee9f5;
  --grey-band:#f1f1f1;
  --topbar:#3b3b3b;
  --white:#fff;
}
*{box-sizing:border-box;margin:0;padding:0}
html,body{width:1200px;height:4865px;overflow:hidden}
body{font-family:"Open Sans",Arial,sans-serif;color:var(--body);background:var(--white);position:relative}
.display{font-family:"Red Hat Display",Arial,sans-serif}
a{color:inherit;text-decoration:none}

/* top bar */
.topbar{height:32px;background:var(--topbar);display:flex;align-items:center;justify-content:space-between;padding:0 88px 0 92px}
.topbar .social{display:flex;gap:14px}
.topbar .social span{width:10px;height:10px;border-radius:50%;background:#bbb;display:block}
.topbar .links{display:flex;gap:26px;font-size:10px;font-weight:600;color:#ddd;text-transform:uppercase}

/* header */
.header{height:114px;display:flex;align-items:center;padding:0 81px 0 92px}
.brand{display:flex;align-items:center;gap:12px;width:400px}
.brand .dot{width:52px;height:52px;border-radius:50%;background:var(--teal)}
.brand .name{font-family:"Red Hat Display",Arial,sans-serif;font-weight:700;font-size:30px;color:var(--teal);line-height:1}
.brand .tag{font-size:11px;color:var(--red);margin-top:5px}
.contact{display:flex;align-items:center;gap:10px;font-size:12px;color:#444;line-height:1.4}
.contact svg{flex:none}
.contact.phone{width:227px}
.contact.addr{width:243px}
.contact b{font-weight:700}

/* nav */
.nav{height:50px;margin:4px 81px 0;display:flex;align-items:center;border-top:1px solid #eee}
.nav ul{display:flex;list-style:none;flex:1;height:100%}
.nav li{font-size:12px;font-weight:700;color:#333;text-transform:uppercase;padding:0 12px;display:flex;align-items:center}
.nav li.active{background:var(--red);color:var(--white)}
.nav .search{width:40px;height:50px;background:var(--red);display:flex;align-items:center;justify-content:center}

/* hero */
.hero{position:absolute;top:204px;left:0;width:1200px;height:574px}
.hero .photo{position:absolute;inset:0;background:linear-gradient(90deg,#eef0ec 0%,#dfe4da 40%,#b9c79b 70%,#8fa66a 100%)}
.hero .copy{position:absolute;left:88px;top:164px;width:420px}
.hero h1{font-family:"Red Hat Display",Arial,sans-serif;font-size:50px;font-weight:800;color:#1d1d1d}
.hero p{font-size:17px;color:#444;margin:14px 0 0 0;line-height:1.45;padding-left:2px}
.hero .btns{display:flex;gap:18px;margin-top:36px}
.btn{display:inline-block;font-size:15px;font-weight:700;color:var(--white);padding:12px 28px}
.btn.teal{background:var(--teal)}
.btn.red{background:var(--red)}

/* services */
.services{position:absolute;top:778px;left:0;width:1200px;height:584px}
.services h2{font-family:"Red Hat Display",Arial,sans-serif;font-size:44px;font-weight:700;color:var(--ink);text-align:center;margin-top:72px}
.service-row{display:flex;justify-content:center;gap:29px;margin-top:60px}
.service{width:230px;text-align:center}
.service .icon{width:150px;height:150px;border-radius:50%;background:var(--teal);margin:0 auto;display:flex;align-items:center;justify-content:center}
.service h3{font-size:17px;font-weight:600;color:var(--red);text-transform:uppercase;margin-top:22px;line-height:1.2}
.service p{font-size:13px;color:var(--body);margin-top:10px;line-height:1.4}
.service .more{display:block;font-size:13px;font-weight:600;color:var(--teal);margin-top:14px}

/* specialise */
.specialise{position:absolute;top:1362px;left:0;width:1200px;height:720px;background:var(--grey-band)}
.spec-block{position:absolute;left:88px;width:680px}
.spec-block h2{font-family:"Red Hat Display",Arial,sans-serif;font-size:27px;font-weight:700;color:var(--teal);margin-bottom:18px}
.spec-block p{font-size:13px;line-height:1.55;margin-bottom:14px}
.promo{position:absolute;left:801px;width:318px;height:243px}
.promo .art{position:absolute;inset:0}
.promo .label{position:absolute;left:0;right:0;bottom:0;height:42px;padding:4px 10px;font-size:13px;font-weight:700;color:var(--white);line-height:1.3}
.promo .headline{position:absolute;font-family:"Red Hat Display",Arial,sans-serif;font-weight:800;line-height:1.05}

/* finder */
.finder{position:absolute;top:2082px;left:0;width:1200px;height:253px;background:linear-gradient(90deg,#27616c,#3b7d8a 50%,#2b5c68)}
.finder h2{font-family:"Red Hat Display",Arial,sans-serif;font-size:38px;font-weight:700;color:var(--white);text-align:center;margin-top:44px}
.finder form{position:absolute;left:81px;top:134px;display:flex;align-items:flex-end;gap:29px}
.field label{display:block;font-size:13px;font-weight:600;color:var(--white);margin-bottom:6px}
.field .input{height:40px;background:var(--white);font-size:12px;color:#999;padding:11px 12px}
.finder .or{font-size:14px;font-weight:700;color:var(--white);padding-bottom:12px}
.finder .submit{width:172px;height:40px;background:var(--red);color:var(--white);font-size:15px;font-weight:700;text-align:center;line-height:40px}

/* video */
.video{position:absolute;top:2432px;left:169px;width:836px;height:471px;background:linear-gradient(90deg,#8aa0a8 0%,#b6c3c4 40%,#d9b48e 70%,#a97c5a 100%)}
.video .play{position:absolute;left:388px;top:186px;width:70px;height:70px;border-radius:50%;background:rgba(0,0,0,.55);display:flex;align-items:center;justify-content:center}
.video .lower-third{position:absolute;left:110px;top:360px;width:290px;padding:6px 12px;background:rgba(255,255,255,.88)}
.video .lower-third small{display:block;font-size:10px;color:#555;text-transform:uppercase}
.video .lower-third strong{font-family:"Red Hat Display",Arial,sans-serif;font-size:20px;color:#333;letter-spacing:1px}
.video .controls{position:absolute;left:0;right:0;bottom:0;height:30px;background:#1b1b1b;display:flex;align-items:center;gap:12px;padding:0 14px;color:#ccc;font-size:11px}
.video .track{flex:1;height:4px;background:#555}
.video .track i{display:block;width:6%;height:100%;background:var(--red)}

/* quote */
.quote-mark{position:absolute;top:2958px;left:574px;width:52px;height:52px;border-radius:50%;background:var(--teal)}
.quote{position:absolute;top:3032px;left:0;width:1200px;height:406px;background:var(--light-blue)}
.quote blockquote{font-size:21px;color:#333;text-align:center;margin-top:138px}
.quote .signoff{position:absolute;left:326px;top:242px;display:flex;gap:28px;align-items:flex-start}
.quote .avatar{width:124px;height:124px;border-radius:50%;border:4px solid var(--white);background:linear-gradient(135deg,#f0d29a,#c9a27a)}
.quote .sig{font-size:12px;line-height:1.5;color:#444;padding-top:8px}

/* blog */
.blog{position:absolute;top:3438px;left:0;width:1200px;height:778px}
.blog h2{font-family:"Red Hat Display",Arial,sans-serif;font-size:44px;font-weight:700;color:var(--ink);text-align:center;margin-top:58px}
.posts{display:flex;gap:33px;position:absolute;left:81px;top:188px}
.post{width:324px}
.post .thumb{height:156px}
.post h3{font-family:"Red Hat Display",Arial,sans-serif;font-size:24px;font-weight:700;color:var(--ink);line-height:1.2;margin-top:20px}
.post .meta{font-size:11px;color:var(--muted);margin-top:8px}
.post .meta em{font-style:normal;color:var(--teal);margin-left:20px}
.post p{font-size:12px;line-height:1.5;color:var(--body);margin-top:8px}
.blog .all{position:absolute;left:505px;top:686px;width:190px;height:38px;border-radius:19px;background:var(--red);color:var(--white);font-size:13px;font-weight:700;text-align:center;line-height:38px;text-transform:uppercase}

/* map */
.map{position:absolute;top:4216px;left:0;width:1200px;height:308px;background:linear-gradient(135deg,#a9cfdc 0%,#c6dde4 40%,#e6e9e4 60%,#dfe3dc 100%)}
.map .pin{position:absolute;left:578px;top:104px}

/* footer */
.footer{position:absolute;top:4524px;left:0;width:1200px;height:341px;background:var(--teal);color:var(--white);text-align:center}
.footer .brand{justify-content:center;width:auto;margin-top:58px}
.footer .brand .dot{width:44px;height:44px;background:var(--white)}
.footer .brand .name{color:var(--white);font-size:28px}
.footer .brand .tag{color:var(--white)}
.footer ul{list-style:none;display:flex;justify-content:center;gap:44px;margin-top:34px;font-size:12px;font-weight:600;text-transform:uppercase}
.footer .copy{font-size:12px;margin-top:16px}
.footer .social{display:flex;justify-content:center;gap:12px;margin-top:20px}
.footer .social span{width:30px;height:30px;border-radius:50%;background:var(--teal-dark);display:block}
</style>
</head>
<body>

<div class="topbar">
  <div class="social"><span></span><span></span><span></span></div>
  <div class="links"><a>Join our associates</a><a>Program marriage counselling</a><a>Relationship counselling</a></div>
</div>

<header class="header">
  <div class="brand">
    <span class="dot"></span>
    <div>
      <div class="name">The Kelvale Clinic</div>
      <div class="tag">helping you create loving relationships</div>
    </div>
  </div>
  <div class="contact phone">
    <svg width="26" height="26" viewBox="0 0 26 26"><circle cx="13" cy="13" r="12" fill="none" stroke="#999" stroke-width="1.5"/><path d="M9 7l3 3-2 2c1 2 2 3 4 4l2-2 3 3-2 2c-5 0-10-5-10-10z" fill="#999"/></svg>
    <div><b>1 300 555 014</b><br>info@kelvaleclinic.com</div>
  </div>
  <div class="contact addr">
    <svg width="26" height="26" viewBox="0 0 26 26"><circle cx="13" cy="13" r="12" fill="none" stroke="#999" stroke-width="1.5"/><path d="M13 6a5 5 0 0 0-5 5c0 4 5 9 5 9s5-5 5-9a5 5 0 0 0-5-5zm0 7a2 2 0 1 1 0-4 2 2 0 0 1 0 4z" fill="#999"/></svg>
    <div><b>41 Marlow Street,</b><br>Suite 20 Brookfield, QLD Australia</div>
  </div>
  <div class="contact hours">
    <svg width="26" height="26" viewBox="0 0 26 26"><circle cx="13" cy="13" r="12" fill="none" stroke="#999" stroke-width="1.5"/><path d="M13 7v6l4 3" fill="none" stroke="#999" stroke-width="2"/></svg>
    <div><b>7:30 AM – 7:30 PM</b><br>Monday to Saturday</div>
  </div>
</header>

<nav class="nav">
  <ul>
    <li class="active">Home</li><li>About</li><li>Resources</li><li>Counselling Types</li><li>Relationship Counselling</li><li>Sex Therapy Locations</li><li>Quizzes</li><li>F.A.Q's</li><li>Blog</li><li>Shop Cart</li>
  </ul>
  <div class="search"><svg width="18" height="18" viewBox="0 0 18 18"><circle cx="7.5" cy="7.5" r="5.5" fill="none" stroke="#fff" stroke-width="2.2"/><path d="M11.5 11.5l5 5" stroke="#fff" stroke-width="2.4"/></svg></div>
</nav>

<section class="hero">
  <div class="photo" role="img" aria-label="Photograph of a smiling family of four outdoors"></div>
  <div class="copy">
    <h1>The Kelvale Clinic</h1>
    <p>is a company passionate about creating healthy loving relationships, of all kinds.</p>
    <div class="btns"><a class="btn teal">Read More</a><a class="btn red">Contact Us</a></div>
  </div>
</section>

<section class="services">
  <h2>Do you need help with:</h2>
  <div class="service-row">
    <div class="service">
      <div class="icon"><svg width="70" height="60" viewBox="0 0 70 60" fill="#fff"><circle cx="35" cy="12" r="8"/><circle cx="14" cy="42" r="7"/><circle cx="56" cy="42" r="7"/><path d="M35 22v10M35 32L14 34M35 32l21 2" stroke="#fff" stroke-width="3" fill="none"/></svg></div>
      <h3>Relationship<br>Counselling</h3>
      <p>Communication, Recovering from an affair, Loss of intimacy &amp; love, Power battles, Feeling like friends, not lovers.</p>
      <a class="more">more details...</a>
    </div>
    <div class="service">
      <div class="icon"><svg width="70" height="70" viewBox="0 0 70 70" fill="none" stroke="#fff" stroke-width="5"><circle cx="28" cy="40" r="14"/><circle cx="44" cy="28" r="14"/><path d="M53 19l10-10M55 9h8v8M28 54v12M22 61h12"/></svg></div>
      <h3>Sex Therapy<br>Counselling</h3>
      <p>Low libido, erectile difficulties, premature ejaculation, differing libidos, porn addiction, keeping sex exciting.</p>
      <a class="more">more details...</a>
    </div>
    <div class="service">
      <div class="icon"><svg width="60" height="70" viewBox="0 0 60 70" fill="#fff"><circle cx="30" cy="30" r="12"/><path d="M14 68c0-14 7-22 16-22s16 8 16 22z"/><path d="M30 4v8M14 10l5 6M46 10l-5 6" stroke="#fff" stroke-width="3"/></svg></div>
      <h3>Anger Management<br>Counselling</h3>
      <p>Managing angry outbursts, expressing your anger in healthy ways.</p>
      <a class="more">more details...</a>
    </div>
    <div class="service">
      <div class="icon"><svg width="60" height="70" viewBox="0 0 60 70" fill="#fff"><circle cx="30" cy="22" r="13"/><path d="M10 68c0-16 9-26 20-26s20 10 20 26z"/></svg></div>
      <h3>Narcissism<br>Counselling</h3>
      <p>Managing narcissistic, superior, entitled, arrogant and lack of empathy tendencies in you or your partner.</p>
      <a class="more">more details...</a>
    </div>
  </div>
</section>

<section class="specialise">
  <div class="spec-block" style="top:58px">
    <h2>We Specialise in Relationship &amp; Marriage Counselling</h2>
    <p>At The Kelvale Clinic, we are a group of PSYCHOLOGISTS, Australia wide who are passionate about relationships and helping you with yours.</p>
    <p>Our vision is to provide the most highly regarded and comprehensive marriage counselling and relationship counselling, and sex therapy in Australia, at reasonable and affordable rates.</p>
    <p>When we are experiencing relationship and marriage problems, there can be a lot of pain and confusion, and it can often be difficult to cope with the other areas of our lives when we are struggling with problems with our partner.</p>
    <p>We are not taught about relationships and how to have a good one in our schools, so most of us are doing the best we know how, but lack the knowledge on how to create a better relationship.</p>
  </div>
  <div class="spec-block" style="top:384px">
    <h2>We Specialise in Relationship &amp; Marriage Counselling</h2>
    <p>At The Kelvale Clinic, we are a group of PSYCHOLOGISTS, Australia wide who are passionate about relationships and helping you with yours.</p>
    <p>Our vision is to provide the most highly regarded and comprehensive marriage counselling and relationship counselling, and sex therapy in Australia, at reasonable and affordable rates.</p>
    <p>When we are experiencing relationship and marriage problems, there can be a lot of pain and confusion, and it can often be difficult to cope with the other areas of our lives when we are struggling with problems with our partner.</p>
    <p>We are not taught about relationships and how to have a good one in our schools, so most of us are doing the best we know how, but lack the knowledge on how to create a better relationship.</p>
  </div>
  <div class="promo" style="top:65px">
    <div class="art" role="img" aria-label="Photograph of a worried woman resting her head on her hand" style="background:linear-gradient(90deg,#fbeaea,#f1d4c8 60%,#e7bfae)"></div>
    <div class="headline" style="left:12px;top:12px;font-size:23px;color:var(--red)">Is Anxiety,<br>Depression<br>or Stress<br>bothering<br>YOU?</div>
    <div class="label" style="background:var(--red)">Click here for help from Kelvale Anxiety &amp; Depression Psychologists</div>
  </div>
  <div class="promo" style="top:357px">
    <div class="art" role="img" aria-label="Photograph of two medical professionals" style="background:linear-gradient(90deg,#dfe9ee,#eef3f5 60%,#f6f8f9)"></div>
    <div class="headline" style="right:12px;top:100px;font-size:19px;color:#1d3d5c;text-align:right">Information<br>for referring<br>GPs &amp; health<br>professionals</div>
    <div class="label" style="background:var(--teal);height:30px;line-height:22px">Click here for more details.</div>
  </div>
</section>

<section class="finder">
  <h2>Find Our Psychologist Near You</h2>
  <form>
    <div class="field"><label>Type of Counselling:</label><div class="input" style="width:237px">Selected</div></div>
    <div class="field"><label>Location:</label><div class="input" style="width:246px"></div></div>
    <div class="or">OR</div>
    <div class="field"><label>Postcode:</label><div class="input" style="width:240px"></div></div>
    <div class="submit">Submit</div>
  </form>
</section>

<div class="video" role="img" aria-label="Video still of the head psychologist speaking beside a couple">
  <div class="play"><svg width="26" height="28" viewBox="0 0 26 28"><path d="M4 2l20 12L4 26z" fill="#fff"/></svg></div>
  <div class="lower-third"><small>Head Psychologist &amp; Director</small><strong>MAREN ELLIS</strong></div>
  <div class="controls"><span>▶</span><span>0:07 / 4:29</span><div class="track"><i></i></div><span>CC</span><span>⚙</span><span>⛶</span></div>
</div>

<div class="quote-mark"></div>
<section class="quote">
  <blockquote>At the end of our life, what matters most is how well did we love"</blockquote>
  <div class="signoff">
    <div class="avatar" role="img" aria-label="Portrait of the clinic director"></div>
    <div class="sig">You can read more about relationship counselling here.<br>Warmly,<br>Maren Ellis<br>Director – Psychologist<br>Grad Dip Psych, Post Grad Dip Psych, B Ed, Dip Teach, MAPS</div>
  </div>
</section>

<section class="blog">
  <h2>Latest Blog Posts</h2>
  <div class="posts">
    <article class="post">
      <div class="thumb" role="img" aria-label="Photograph of a distressed woman in a counselling session" style="background:linear-gradient(90deg,#c9b8a4,#e3d7c5)"></div>
      <h3>What can I do if I'm living with a Narcissist?</h3>
      <div class="meta">June 23, 2016 at 8:52pm <em>Chiropractic</em></div>
      <p>Chiropractors are best known for safety and effectively treating acute back and neck pain, as well as headaches. Whereas a medical doctor...</p>
    </article>
    <article class="post">
      <div class="thumb" role="img" aria-label="Photograph of a couple sitting apart after an argument" style="background:linear-gradient(90deg,#b79b86,#d9c4b0)"></div>
      <h3>How Do I Know If I'm With a Narcissist?</h3>
      <div class="meta">June 23, 2016 at 8:52pm <em>Healthy Lifestyle</em></div>
      <p>About 2 months ago, I was participating in my morning class at a local gym, partaking in a killer WOD (workout of the day) that required a lot of heavy squats...</p>
    </article>
    <article class="post">
      <div class="thumb" role="img" aria-label="Photograph of a couple sitting apart on a sofa" style="background:linear-gradient(90deg,#cfd8c4,#e8ece2)"></div>
      <h3>Did Your Relationship Start on Rocky Ground?</h3>
      <div class="meta">June 23, 2016 at 8:52pm <em>Heart Health</em></div>
      <p>Heart disease is the number one cause of death in the U.S. How many people do you know that have been personally affected by heart disease? I'm guessing the number...</p>
    </article>
  </div>
  <a class="all">View all blog posts</a>
</section>

<div class="map" role="img" aria-label="Street map showing the clinic location">
  <svg class="pin" width="44" height="62" viewBox="0 0 44 62"><path d="M22 0C10 0 0 10 0 22c0 16 22 40 22 40s22-24 22-40C44 10 34 0 22 0z" fill="var(--teal)"/><circle cx="22" cy="22" r="8" fill="#fff"/></svg>
</div>

<footer class="footer">
  <div class="brand">
    <span class="dot"></span>
    <div style="text-align:left">
      <div class="name">The Kelvale Clinic</div>
      <div class="tag">helping you create loving relationships</div>
    </div>
  </div>
  <ul><li>Home</li><li>About</li><li>Resources</li><li>Blog</li><li>Shop Cart</li></ul>
  <div class="copy">Copyright © 2016,TheKelvaleClinic . All rights reserved</div>
  <div class="social"><span></span><span></span><span></span><span></span></div>
</footer>

</body>
</html>
```